Brand Identity Stationary Package

Hello I'm looking for a full branding package for my Property Management Company. I have a logo but looking to have the following
Business Card
Email signature
Facebook cover photo
Letterhead (word.doc)
#10 Envelope
Pocket Folder - link to 9x12 pocket folder design specs https://www.printorbit-example.ca/marketing-materials/presentation-folders
would like everything to match and be brand identifiable. The company looks after residential properties/apartments and some commercial properties. Attached is a zip of the files.
For Business Card
Name: Gareth Lindqvist
Position: Operations Manager
Number: 1 (555) 384-2917
Email: Gareth@harborkey-example.ca
Website: Harborkey-example.ca
Property Management

```html
<!DOCTYPE html>
<html lang="en">
<head>
<meta charset="utf-8">
<title>Harborkey Business Card</title>
<link rel="stylesheet" href="https://fonts.googleapis.com/css2?family=Arimo:wght@400;700&display=swap">
<style>
  :root {
    --backdrop: #2b2b2b;
    --card-light: #ececec;
    --card-dark: #1d1a1b;
    --ink: #262626;
    --ink-soft: #3d3d3d;
    --brand-green: #6a9a2e;
    --divider: #9a9a9a;
    --emboss: #2e2b2c;
  }
  html, body {
    margin: 0;
    padding: 0;
    width: 1200px;
    height: 896px;
    overflow: hidden;
    background: var(--backdrop);
    font-family: "Arimo", Arial, sans-serif;
  }
  .stage {
    position: relative;
    width: 1200px;
    height: 896px;
  }
  .card {
    position: absolute;
    left: 353px;
    width: 485px;
    height: 278px;
    box-shadow: 0 10px 24px rgba(0,0,0,0.45);
  }
  .card-front { top: 160px; background: var(--card-light); }
  .card-back { top: 469px; background: var(--card-dark); }

  .front-wordmark {
    position: absolute;
    left: 39px;
    top: 118px;
    font-weight: 700;
    font-size: 27px;
    letter-spacing: 2px;
    color: var(--ink);
    text-transform: uppercase;
  }
  .front-divider {
    position: absolute;
    left: 243px;
    top: 90px;
    width: 1px;
    height: 98px;
    background: var(--divider);
  }
  .contact-block {
    position: absolute;
    left: 266px;
    top: 88px;
  }
  .person-name {
    margin: 0;
    font-size: 15.5px;
    font-weight: 700;
    color: var(--brand-green);
  }
  .person-role {
    margin: 3px 0 0;
    font-size: 11.5px;
    color: var(--ink-soft);
  }
  .contact-list {
    list-style: none;
    margin: 22px 0 0;
    padding: 0;
  }
  .contact-item {
    display: flex;
    align-items: center;
    gap: 7px;
    height: 17.5px;
    font-size: 11px;
    color: var(--ink-soft);
  }
  .contact-icon { width: 9px; height: 9px; flex: none; }

  .back-wordmark {
    position: absolute;
    left: 0;
    right: 0;
    top: 112px;
    text-align: center;
    font-weight: 700;
    font-size: 40px;
    letter-spacing: 3px;
    color: var(--emboss);
    text-transform: uppercase;
  }
</style>
</head>
<body>
<main class="stage">
  <section class="card card-front">
    <div class="front-wordmark">Harborkey</div>
    <div class="front-divider"></div>
    <div class="contact-block">
      <h1 class="person-name">Gareth Lindqvist</h1>
      <p class="person-role">Operations Manager</p>
      <ul class="contact-list">
        <li class="contact-item">
          <svg class="contact-icon" viewBox="0 0 10 10" aria-hidden="true"><path d="M2 0.5 L3.6 2.8 L2.8 3.8 C3.4 5.2 4.6 6.4 6.2 7.2 L7.2 6.4 L9.5 8 L8.6 9.5 C4.5 9.3 0.7 5.5 0.5 1.4 Z" fill="var(--brand-green)"/></svg>
          <span>1 (555) 384-2917</span>
        </li>
        <li class="contact-item">
          <svg class="contact-icon" viewBox="0 0 10 10" aria-hidden="true"><rect x="0.6" y="1.8" width="8.8" height="6.4" fill="none" stroke="var(--brand-green)" stroke-width="1"/><path d="M0.6 1.8 L5 5.6 L9.4 1.8 M0.6 8.2 L4 5 M9.4 8.2 L6 5" fill="none" stroke="var(--brand-green)" stroke-width="0.8"/></svg>
          <span>Gareth@harborkey-example.ca</span>
        </li>
        <li class="contact-item">
          <svg class="contact-icon" viewBox="0 0 10 10" aria-hidden="true"><circle cx="5" cy="5" r="4.4" fill="none" stroke="var(--brand-green)" stroke-width="1"/><ellipse cx="5" cy="5" rx="2" ry="4.4" fill="none" stroke="var(--brand-green)" stroke-width="0.8"/><path d="M0.6 5 H9.4" stroke="var(--brand-green)" stroke-width="0.8"/></svg>
          <span>www.Harborkey-example.ca</span>
        </li>
      </ul>
    </div>
  </section>

  <section class="card card-back">
    <div class="back-wordmark">Harborkey</div>
  </section>
</main>
</body>
</html>
```